Help our Sugar Loom find our winning design! We're looking for a business card....

We’re a Sugar Loom in NY specializing in custom-made cakes and unique desserts.
Our cakes combine flavor and art, each designed to match customer’s special event and theme.
We’d like a unique business card with a clean design that will combine French chic and artistic look & feel.
We’d like to differentiate ourselves from standard bakeries, please don’t offer cupcake images :-)
Our logo is peach-pink and brown and we’d love to use these colors ( . Another color that can be added is gold - or feel free to suggest!

Target Market(s)

Women, ages 25-55

Industry/Entity Type

Boutique

Contact Information for Business Card

Text on card:
Logo
Sugar Loom by Dana Welch

www.sugarloomsweets.com
hello@sugarloom.com
(516) 555-0147
F – sugarloomnyc
IG - sugarloom_ny

Font styles to use
Sans Serif
Script

Requirements
Must have
• Logo
• Clean look
• French chic and artistic look & feel.
Nice to have
• Damask pattern
Should not have
• Cupcake images

```html
<!DOCTYPE html>
<html lang="en">
<head>
<meta charset="utf-8">
<title>Sugar Loom – Business Card</title>
<link href="https://fonts.googleapis.com/css2?family=Open+Sans:wght@400;600&family=Pinyon+Script&display=swap" rel="stylesheet">
<style>
  :root {
    --backdrop: #c9c9c9;
    --card: #ffffff;
    --peach: #d8a99c;
    --cocoa: #3b2b27;
    --ink: #2b2b2b;
  }
  * { box-sizing: border-box; margin: 0; padding: 0; }
  html, body {
    width: 1200px; height: 852px; overflow: hidden;
    background: var(--backdrop);
    font-family: "Open Sans", Arial, sans-serif;
    color: var(--ink);
  }
  .stage { position: relative; width: 1200px; height: 852px; }
  .card {
    position: absolute;
    width: 500px; height: 286px;
    background: var(--card);
    border-radius: 26px;
    box-shadow: 0 6px 14px rgba(0,0,0,.25);
    overflow: hidden;
  }
  .card--front { left: 90px; top: 150px; }
  .card--back  { left: 610px; top: 416px; }

  .brand {
    position: absolute;
    display: flex; align-items: center; gap: 10px;
    font-family: "Open Sans", Arial, sans-serif;
    font-weight: 400;
    color: var(--cocoa);
    letter-spacing: .02em;
  }
  .brand__dot {
    width: 12px; height: 12px; border-radius: 50%;
    background: var(--peach);
  }
  .card--front .brand { left: 0; right: 0; top: 118px; justify-content: center; font-size: 40px; }
  .card--back .brand { right: 36px; top: 44px; font-size: 28px; }

  .divider {
    position: absolute; left: 180px; right: 30px; top: 128px;
    height: 1px; background: var(--peach);
  }
  .owner { position: absolute; left: 34px; top: 150px; }
  .owner__label { font-size: 14px; color: var(--ink); }
  .owner__name {
    font-family: "Pinyon Script", cursive;
    font-size: 28px; line-height: 1.1; color: var(--cocoa);
  }
  .contacts { position: absolute; left: 34px; top: 212px; list-style: none; }
  .contacts li, .socials li {
    display: flex; align-items: center; gap: 8px;
    font-size: 13px; line-height: 19px; color: var(--ink);
  }
  .contacts svg { width: 12px; height: 12px; fill: var(--cocoa); }
  .socials { position: absolute; right: 30px; top: 142px; list-style: none; }
  .socials__mark { width: 11px; height: 11px; background: var(--cocoa); border-radius: 2px; }
</style>
</head>
<body>
<main class="stage">
  <section class="card card--front" aria-label="Card front">
    <div class="brand"><span class="brand__dot"></span>Sugar Loom</div>
  </section>

  <section class="card card--back" aria-label="Card back">
    <div class="brand"><span class="brand__dot"></span>Sugar Loom</div>
    <div class="divider"></div>

    <ul class="socials">
      <li><span class="socials__mark"></span>sugarloomnyc</li>
      <li><span class="socials__mark"></span>sugarloom_ny</li>
    </ul>

    <div class="owner">
      <p class="owner__label">Sugar Loom by</p>
      <p class="owner__name">Dana Welch</p>
    </div>

    <ul class="contacts">
      <li>
        <svg viewBox="0 0 12 12" aria-hidden="true"><path d="M2 1h3l1 3-2 1c.6 1.4 1.6 2.4 3 3l1-2 3 1v3c-5.5 0-9-3.5-9-9z"/></svg>
        (516) 555-0147
      </li>
      <li>
        <svg viewBox="0 0 12 12" aria-hidden="true"><path d="M0 2h12v8H0z M1 3l5 3.5L11 3" stroke="#fff" stroke-width="1"/></svg>
        hello@sugarloom.com
      </li>
      <li>
        <svg viewBox="0 0 12 12" aria-hidden="true"><circle cx="6" cy="6" r="5.5"/><path d="M.5 6h11M6 .5v11M2 3h8M2 9h8" stroke="#fff" stroke-width=".8" fill="none"/></svg>
        www.sugarloomsweets.com
      </li>
    </ul>
  </section>
</main>
</body>
</html>
```